Company or website name
- dalewintham.com
- Links to the website
- Vita Forge
- Describe your company and organization and target audience
- Founded by celebrity personal trainer and media personality Dale Wintham, Vita Forge provides high quality on-site fitness and wellness classes, and personal trainers for businesses and residential gyms throughout New York City. Our target audience are residents of high end buildings in NYC, that expect excellence and luxury
- The design should have the following
- This is a 24"x36" Poster for a complimentary event at a high end building. I would like the poster to look high end, luxury and simple and chique. The words should be clear and easy to read. It would be great to have a final copy that we can send to the printer and one which we can edit for future events Here is the text: The Halcott Spires Gym Complimentary Fitness & Wellness Event Complimentary Yoga, Pilates & Interval Training Bootcamp Classes PLUS: 30 Minute Private Training Sessions *Kids Karate Classes Also Available Saturday May 18th, 25th & June 1st Time: 9:00am - 12:15pm Halcott Spires Gym Schedule: 9:00am - 9:30am Yoga 9:45am - 10:15am Interval Training Bootcamp 11:45am -12:15pm Pilates 9:00am - 12:00pm Private Training Sessions Special Introductory Rate on Future Packages During Promotion www.Vitaforge.tv Info@vitaforge.tv
- Other Facts

```html
<!DOCTYPE html>
<html lang="en">
<head>
<meta charset="utf-8">
<title>The Halcott Spires Gym – Complimentary Fitness &amp; Wellness Event</title>
<link href="https://fonts.googleapis.com/css2?family=Jost:wght@400;500;600;700&display=swap" rel="stylesheet">
<style>
  :root {
    --page: #ffffff;
    --lime: #a6cb22;
    --lime-dark: #17602d;
    --ink: #1c1a1a;
    --banner: #0a78c2;
    --banner-dark: #2d3f8c;
    --sky: #1aa0dd;
    --gold: #ffd400;
    --white: #ffffff;
    --text-dark: #2a2a2a;
  }
  html, body {
    margin: 0;
    padding: 0;
    width: 1200px;
    height: 961px;
    overflow: hidden;
    background: var(--page);
    font-family: "Jost", "Century Gothic", sans-serif;
  }
  .canvas {
    position: relative;
    width: 1200px;
    height: 961px;
  }
  .poster {
    position: absolute;
    left: 280px;
    top: 0;
    width: 640px;
    height: 961px;
    background: var(--lime);
    overflow: hidden;
    box-shadow: 0 0 14px rgba(0,0,0,0.18);
  }
  .main-panel {
    position: absolute;
    left: 25px;
    top: 24px;
    width: 590px;
    height: 617px;
    background: var(--ink);
  }
  .schedule-band {
    position: absolute;
    left: 0;
    top: 641px;
    width: 640px;
    height: 237px;
    background: var(--white);
    border-top: 2px solid var(--gold);
    border-bottom: 2px solid var(--gold);
    box-sizing: border-box;
  }
  .footer-panel {
    position: absolute;
    left: 25px;
    top: 881px;
    width: 590px;
    height: 55px;
    background: var(--ink);
  }
  .corner {
    position: absolute;
  }
  .brand {
    position: absolute;
    left: 40px;
    top: 48px;
    display: flex;
    align-items: center;
    gap: 10px;
    color: var(--white);
    font-weight: 600;
    font-size: 22px;
    letter-spacing: 0.5px;
  }
  .brand-dot {
    width: 40px;
    height: 40px;
    border: 3px solid var(--white);
    border-radius: 50%;
    box-sizing: border-box;
  }
  .banner {
    position: absolute;
    left: -40px;
    top: 105px;
    width: 720px;
    height: 102px;
    background: var(--banner);
    transform: rotate(-6.5deg);
    transform-origin: 50% 50%;
    box-shadow: 0 3px 0 var(--banner-dark);
  }
  .banner-text {
    position: absolute;
    left: 90px;
    top: 14px;
    width: 544px;
    color: var(--white);
    text-transform: uppercase;
  }
  .banner-title {
    font-weight: 600;
    font-size: 40px;
    line-height: 44px;
    letter-spacing: 1.5px;
    white-space: nowrap;
  }
  .banner-subtitle {
    text-align: right;
    font-weight: 500;
    font-size: 16px;
    line-height: 20px;
    letter-spacing: 1px;
    margin-top: -8px;
  }
  .athlete-photo {
    position: absolute;
    left: 65px;
    top: 182px;
    width: 232px;
    height: 725px;
  }
  .offer {
    position: absolute;
    right: 61px;
    text-align: right;
    margin: 0;
  }
  .classes {
    top: 244px;
    color: var(--white);
    font-weight: 500;
    font-size: 23px;
    line-height: 28px;
    letter-spacing: 0.5px;
    text-transform: uppercase;
  }
  .bonus {
    top: 374px;
    color: var(--white);
  }
  .bonus-label {
    display: block;
    color: var(--gold);
    font-weight: 600;
    font-size: 30px;
    line-height: 34px;
  }
  .bonus-headline {
    display: block;
    font-weight: 600;
    font-size: 48px;
    line-height: 46px;
  }
  .bonus-detail {
    display: block;
    font-weight: 500;
    font-size: 19px;
    line-height: 24px;
  }
  .promo {
    top: 517px;
    color: var(--gold);
    font-weight: 500;
    font-size: 21px;
    line-height: 26px;
  }
  .dates {
    position: absolute;
    right: 27px;
    top: 661px;
    text-align: right;
    margin: 0;
  }
  .dates-day {
    display: block;
    color: var(--sky);
    font-weight: 500;
    font-size: 44px;
    line-height: 48px;
  }
  .dates-list {
    display: block;
    color: var(--text-dark);
    font-weight: 500;
    font-size: 29px;
    line-height: 34px;
  }
  .timetable {
    position: absolute;
    right: 27px;
    top: 757px;
    border-collapse: collapse;
    font-size: 18px;
    font-weight: 500;
  }
  .timetable td {
    padding: 0;
    height: 25px;
    line-height: 25px;
  }
  .timetable .session {
    text-align: right;
    color: var(--text-dark);
    padding-right: 8px;
  }
  .timetable .time {
    text-align: right;
    color: var(--sky);
    white-space: nowrap;
  }
  .contact {
    position: absolute;
    top: 893px;
    color: var(--white);
    font-size: 16px;
    font-weight: 500;
    line-height: 22px;
  }
  .contact-email { left: 221px; }
  .contact-web { left: 425px; }
</style>
</head>
<body>
<div class="canvas">
  <section class="poster">
    <div class="main-panel"></div>
    <div class="schedule-band"></div>
    <div class="footer-panel"></div>

    <svg class="corner" style="left:0;top:878px" width="25" height="22" viewBox="0 0 25 22"><polygon points="0,0 25,0 25,22" fill="var(--lime-dark)"/></svg>
    <svg class="corner" style="left:615px;top:878px" width="25" height="22" viewBox="0 0 25 22"><polygon points="0,0 25,0 0,22" fill="var(--lime-dark)"/></svg>

    <div class="brand">
      <span class="brand-dot"></span>
      <span class="brand-name">Vita Forge</span>
    </div>

    <div class="banner">
      <div class="banner-text">
        <div class="banner-title">The Halcott Spires Gym</div>
        <div class="banner-subtitle">Complimentary Fitness &amp; Wellness Event</div>
      </div>
    </div>

    <svg class="athlete-photo" role="img" aria-label="Photo of a female athlete in black sportswear mid kick, throwing a punch" viewBox="0 0 232 725" preserveAspectRatio="none">
      <defs>
        <linearGradient id="athleteTone" x1="0" y1="0" x2="0" y2="1">
          <stop offset="0" stop-color="#8a5a3c"/>
          <stop offset="0.45" stop-color="#a86f4a"/>
          <stop offset="0.7" stop-color="#3a2c26"/>
          <stop offset="1" stop-color="#2a2a2a"/>
        </linearGradient>
      </defs>
      <rect x="0" y="0" width="232" height="725" rx="60" fill="url(#athleteTone)" opacity="0.55"/>
    </svg>

    <p class="offer classes">Complimentary Yoga<br>Pilates &amp; Interval Training<br>Bootcamp Classes</p>

    <p class="offer bonus">
      <span class="bonus-label">PLUS FREE:</span>
      <span class="bonus-headline">30 Minute</span>
      <span class="bonus-detail">Private Training Sessions</span>
    </p>

    <p class="offer promo">Special Introductory<br>Rate on Future Packages<br>During Promotion</p>

    <p class="dates">
      <span class="dates-day">Saturday May</span>
      <span class="dates-list">18th, 25th &amp; June 1st</span>
    </p>

    <table class="timetable">
      <tr><td class="session">Yoga</td><td class="time">9:45am - 10:15am</td></tr>
      <tr><td class="session">Interval Training Bootcamp</td><td class="time">11:45am - 12:15pm</td></tr>
      <tr><td class="session">Pilates</td><td class="time">9:00am - 12:00pm</td></tr>
      <tr><td class="session">Halcott Spires Gym</td><td class="time">9:00am &nbsp;- &nbsp;9:30am</td></tr>
    </table>

    <span class="contact contact-email">Info@vitaforge.tv</span>
    <span class="contact contact-web">www.Vitaforge.tv</span>
  </section>
</div>
</body>
</html>
```